Desktop and Networking Support Course 9.17.25

Important the ad should not be very busy with the text taking up the major part of the ad .. please do not make the text so big that it takes up most of the ad..
Flyer Design Brief for Graphic Artist
also i am looking for something unique or creative that it will stand out .
Size & Layout:
Full Page with Bleed: 8” x 10.75” + 0.25” bleed on all sides.
Footer Space: Leave a 1-inch margin at the bottom for footer content (e.g., contact info, logo, or call-to-action).
Target Audience:
College-age students (around 24 years old)
Located in the USA
Interested in creative, professional, and career-building opportunities
Purpose:
To attract students to enroll in a college program
Flyer should be eye-catching, unique, and creative
Text must be clear and readable,
Design Style:
Use vector art, typography, or photography — your choice
If using photography, feature a white young professional USA citizen:
Wearing a white collared shirt
not with long hair
Creative Direction:
The flyer should stand out visually — something people would want to look at and keep
Showcase creativity and professionalism
Use bold colors, dynamic layout, or unexpected design elements to grab attention
Avoid clutter — keep the design balanced and clean
Text Suggestions (can be adjusted):
Footer,
please leave one inch on the bottom for the footer

```html
<!DOCTYPE html>
<html lang="en">
<head>
<meta charset="UTF-8">
<title>Desktop &amp; Network Support Course Flyer</title>
<link href="https://fonts.googleapis.com/css2?family=Anton&family=Poppins:wght@400;600;700&display=swap" rel="stylesheet">
<style>
  :root {
    --orange: #f37121;
    --blue: #2d66b1;
    --ink: #222831;
    --paper: #ffffff;
    --backdrop: #f2f3f5;
    --photo-tone: #b9c6d3;
  }
  * { margin: 0; padding: 0; box-sizing: border-box; }
  html, body { width: 1200px; height: 1200px; overflow: hidden; background: var(--backdrop); }
  body { position: relative; font-family: "Poppins", sans-serif; }

  .flyer {
    position: absolute; left: 173px; top: 0;
    width: 853px; height: 1200px;
    background: var(--paper); overflow: hidden;
  }
  .flyer > * { position: absolute; }

  .cap-art {
    left: 40px; top: 72px; width: 110px; height: 150px;
    border-radius: 18px;
    background: linear-gradient(150deg, #3a74c2, var(--blue));
  }
  .pencil-art {
    left: 690px; top: 200px; width: 150px; height: 34px;
    border-radius: 17px; background: var(--orange);
    transform: rotate(-45deg); transform-origin: left center;
  }

  .headline { left: 168px; top: 70px; font-family: "Anton", sans-serif; line-height: 1; }
  .headline .line-top { display: block; color: var(--orange); font-size: 84px; letter-spacing: 1px; }
  .headline .line-bottom { display: block; color: var(--blue); font-size: 58px; letter-spacing: 3.4px; margin-top: 2px; }
  .cursor { left: 459px; top: 194px; width: 34px; height: 42px; }

  .course-title {
    left: 0; width: 853px; top: 248px; text-align: center;
    color: var(--orange); font-weight: 700; font-size: 40px; line-height: 1.3;
  }

  .photo {
    left: 380px; top: 360px; width: 473px; height: 692px;
    background:
      linear-gradient(to right, var(--paper) 0%, rgba(255,255,255,0) 45%),
      linear-gradient(to bottom, var(--paper) 0%, rgba(255,255,255,0) 18%),
      linear-gradient(160deg, #dfe7ef 0%, var(--photo-tone) 55%, #8a9aab 100%);
  }

  .highlights { left: 40px; top: 340px; list-style: none; }
  .highlights li {
    position: absolute; left: 0; white-space: nowrap;
    padding-left: 37px; color: var(--blue); font-weight: 600; font-size: 24px; line-height: 36px;
  }
  .highlights li::before {
    content: ""; position: absolute; left: 4px; top: 12px;
    width: 12px; height: 12px; border: 3px solid var(--orange); transform: rotate(45deg);
  }

  .ranking-box {
    left: 40px; top: 584px; width: 446px; height: 190px;
    background: var(--blue); border-radius: 20px;
    display: flex; align-items: center; justify-content: center; text-align: center;
    color: var(--paper); font-weight: 700; font-size: 28px; line-height: 1.38; padding: 0 12px;
  }

  .delivery { left: 40px; top: 796px; }
  .delivery .tick { position: absolute; left: 0; top: 30px; width: 24px; height: 20px; }
  .delivery .mode { display: block; margin-left: 34px; color: var(--orange); font-weight: 700; font-size: 30px; line-height: 1.1; }
  .delivery .options { display: block; margin-left: 34px; color: var(--blue); font-weight: 600; font-size: 26px; line-height: 1.3; }

  .enroll-button {
    left: 40px; top: 910px; width: 200px; height: 52px;
    background: var(--blue); border-radius: 4px;
    color: var(--paper); font-weight: 700; font-size: 23px; line-height: 52px; text-align: center;
  }
  .scholarship { left: 40px; top: 980px; color: var(--orange); font-weight: 700; font-size: 30px; line-height: 1.3; }

  .footer-band { left: 0; top: 1052px; width: 853px; height: 148px; background: var(--blue); }
  .contact-pill {
    left: 39px; top: 1074px; width: 775px; height: 62px;
    background: var(--paper); border-radius: 31px;
    display: flex; align-items: center; justify-content: space-between; padding: 0 22px 0 17px;
    color: var(--ink); font-size: 18px;
  }
  .contact-item { display: flex; align-items: center; gap: 14px; white-space: nowrap; }
  .contact-icon { width: 24px; height: 24px; flex: none; }
</style>
</head>
<body>
  <main class="flyer">
    <div class="cap-art" role="img" aria-label="Graduation cap illustration"></div>

    <h1 class="headline">
      <span class="line-top">YOUR CAREER IS</span>
      <span class="line-bottom">JUST A CLICK AWAY</span>
    </h1>
    <svg class="cursor" viewBox="0 0 34 42" aria-hidden="true">
      <path d="M2 2 L30 20 L18 22 L26 38 L20 41 L12 25 L4 33 Z" fill="var(--orange)"/>
    </svg>

    <div class="pencil-art" role="img" aria-label="Pencil illustration"></div>

    <h2 class="course-title">Desktop &amp; Network Support Course</h2>

    <div class="photo" role="img" aria-label="Young professional in a white collared shirt working at a desktop computer"></div>

    <ul class="highlights">
      <li style="top:0">90% Employment Rate – Class of 2024</li>
      <li style="top:40px">Master Nimbus Operating Systems</li>
      <li style="top:90px">Hands-On Desktop &amp; Network Training</li>
      <li style="top:140px">Real-World Troubleshooting Skills</li>
      <li style="top:188px">Ready for IT Jobs</li>
    </ul>

    <div class="ranking-box">Prepare for 3 of the Top 10 Tech Jobs (National Careers Review 2025)</div>

    <div class="delivery">
      <svg class="tick" viewBox="0 0 24 20" aria-hidden="true">
        <path d="M2 10 L9 17 L22 3" fill="none" stroke="var(--orange)" stroke-width="3.5" stroke-linecap="round" stroke-linejoin="round"/>
      </svg>
      <span class="mode">IN-PERSON</span>
      <span class="options">and Remote Options</span>
    </div>

    <div class="enroll-button">Enroll Today!</div>
    <p class="scholarship">Partial Scholarships Offered</p>

    <footer class="footer-band"></footer>
    <div class="contact-pill">
      <span class="contact-item">
        <svg class="contact-icon" viewBox="0 0 24 24" aria-hidden="true">
          <circle cx="12" cy="12" r="12" fill="var(--orange)"/>
          <path d="M8 6.5 L10 6 L11 9 L9.8 10.2 C10.5 11.8 12 13.3 13.7 14 L15 12.8 L18 13.8 L17.5 16 C12 16.5 7.3 11.8 8 6.5 Z" fill="#fff"/>
        </svg>00 2468 13579</span>
      <span class="contact-item">
        <svg class="contact-icon" viewBox="0 0 24 24" aria-hidden="true">
          <circle cx="12" cy="12" r="12" fill="var(--orange)"/>
          <rect x="6.5" y="8" width="11" height="8" fill="none" stroke="#fff" stroke-width="1.4"/>
          <path d="M6.5 8 L12 12.5 L17.5 8" fill="none" stroke="#fff" stroke-width="1.4"/>
        </svg>hello@brightpathtech.edu</span>
      <span class="contact-item">
        <svg class="contact-icon" viewBox="0 0 24 24" aria-hidden="true">
          <circle cx="12" cy="12" r="12" fill="var(--orange)"/>
          <circle cx="12" cy="12" r="6" fill="none" stroke="#fff" stroke-width="1.3"/>
          <ellipse cx="12" cy="12" rx="2.6" ry="6" fill="none" stroke="#fff" stroke-width="1.3"/>
          <path d="M6 12 H18" stroke="#fff" stroke-width="1.3"/>
        </svg>www.brightpathtech.edu</span>
    </div>
  </main>
</body>
</html>
```